Website Development for vaultmerrow.com.au

Build a new Wordpress/Responsive website for vaultmerrow.com.au

Target Market(s)

Compliance Managers, Risk Managers, Information Security and Cyber Security Professionals, Chief Data/Digital Officers, Chief Operating/Financial Officers, Business Continuity Professionals, Disaster Recovery Planners, Small Business Owners, Local/Federal Government entities

Industry/Entity Type

Data Service

Coding

Coded - Design and coding required

Number of Pages Required

5+ page

Font styles to use
Sans Serif

Colors

Designer to choose colors to be used in the design.

Requirements
Must have
• 1. Site Structure: Home Page plus the following chapter-pages for a) Services b) About c) Resources d) Blog e) Contact Us
• 2. Prefer site to built on wordpress and we can purchase a theme if needed (we currently use Kelp9 for other sites)
• 3. Blog needs to be wordpress based
• 4. We will host the site ourselves on our own servers
• 5. Responsive Design
Nice to have
• 1. Livechat capability/interface
• 2. Capability for marketing automation integration (such as hubspot, marketo, infusionsoft etc)
• 3. Capability for CRM integration (Salesforce)

```html
<!DOCTYPE html>
<html lang="en">
<head>
<meta charset="utf-8">
<title>Vaultmerrow</title>
<link rel="stylesheet" href="https://fonts.googleapis.com/css2?family=Montserrat:wght@400;600;700&family=Open+Sans:wght@400;600&display=swap">
<style>
:root{
  --red:#e0101e;
  --dark:#1d1d1f;
  --text:#333;
  --muted:#666;
  --line:#dcdcdc;
  --ghost:#f1f1f1;
  --gray-bg:#efefef;
  --white:#fff;
}
*{margin:0;padding:0;box-sizing:border-box}
html,body{width:1200px;height:4762px;overflow:hidden;background:var(--white)}
body{font-family:"Open Sans",sans-serif;color:var(--text);position:relative}
.abs{position:absolute}
h1,h2,h3,h4,.brand,.nav,.btn{font-family:"Montserrat",sans-serif}

/* header */
.site-header{position:absolute;top:0;left:0;width:1200px;height:110px}
.brand{position:absolute;left:175px;top:30px;display:flex;align-items:center;gap:10px;font-weight:700;font-size:30px;color:var(--red);letter-spacing:1px}
.brand .mark{width:26px;height:26px;background:var(--red);border-radius:50%}
.call{position:absolute;right:175px;top:26px;font-family:"Montserrat",sans-serif;font-weight:700;font-size:18px;color:var(--red);display:flex;align-items:center;gap:6px}
.nav{position:absolute;right:175px;top:72px;display:flex;gap:28px;font-size:14px;font-weight:600;color:#444;letter-spacing:.5px}

/* hero */
.hero{position:absolute;top:110px;left:0;width:1200px;height:605px;overflow:hidden}
.hero-photo{position:absolute;inset:0;background:linear-gradient(100deg,#f4f4f4 0%,#dcdcdc 40%,#8a8d92 70%,#4e5156 100%)}
.hero-shape{position:absolute;left:0;top:0}
.hero h1{position:absolute;left:175px;top:172px;font-size:44px;font-weight:600;color:var(--dark)}
.hero p{position:absolute;left:175px;top:236px;width:380px;font-size:14px;line-height:1.5;color:#555}
.btn{position:absolute;display:inline-block;background:var(--red);color:#fff;font-weight:700;font-size:13px;border-radius:22px;text-align:center}
.hero .btn{left:175px;top:300px;width:150px;height:38px;line-height:38px}
.dots{position:absolute;left:508px;top:500px;display:flex;gap:6px}
.dots span{width:38px;height:3px;background:rgba(255,255,255,.6)}
.dots span.on{background:#fff}

/* section titles */
.ghost{position:absolute;left:0;width:1200px;text-align:center;font-family:"Montserrat",sans-serif;font-weight:700;font-size:96px;color:var(--ghost);letter-spacing:2px}
.section-title{position:absolute;left:0;width:1200px;text-align:center;font-size:32px;font-weight:600;color:var(--dark);letter-spacing:1px}

/* services */
.service{position:absolute;width:270px}
.service .icon{width:58px;height:58px;background:#fbe1e3;border:2px solid var(--red);border-radius:6px}
.service h3{margin-top:22px;font-size:16px;font-weight:600;color:var(--dark)}
.service h3 span{color:var(--red)}
.service p{margin-top:12px;font-size:12px;line-height:1.7;color:var(--muted)}
.rule-h{position:absolute;height:1px;background:var(--line);left:175px;width:855px}
.rule-v{position:absolute;width:1px;background:var(--line)}

/* about */
.about-art{position:absolute;left:175px;top:1842px;width:413px;height:540px;border-radius:40px 40px 200px 200px;background:radial-gradient(circle at 50% 40%,#8d9096 0%,#45484e 55%,#26282c 100%);box-shadow:-10px 10px 0 #f3c5c8}
.about-lead{position:absolute;left:625px;top:1875px;width:400px;font-family:"Montserrat",sans-serif;font-weight:600;font-size:18px;line-height:1.35;color:var(--red)}
.about-copy{position:absolute;left:625px;width:400px;font-size:12px;line-height:1.75;color:var(--muted)}

/* resources */
.resources-bg{position:absolute;top:2461px;left:0;width:1200px;height:730px;background:var(--gray-bg)}
.res-card{position:absolute;width:272px;height:196px;overflow:hidden}
.res-card .ph{position:absolute;inset:0}
.res-card h4{position:absolute;left:20px;bottom:16px;width:220px;color:#fff;font-size:16px;font-weight:600;line-height:1.3}

/* blog */
.blog-intro{position:absolute;left:300px;top:3368px;width:600px;text-align:center;font-size:12px;line-height:1.7;color:var(--muted)}
.blog-hero{position:absolute;left:175px;top:3445px;width:476px;height:476px}
.blog-hero .ph{position:absolute;left:0;top:0;width:476px;height:340px;background:linear-gradient(135deg,#0b2a4a 0%,#12548a 50%,#0a1c33 100%)}
.blog-box{position:absolute;left:15px;top:318px;width:400px;height:158px;background:#fff;box-shadow:0 4px 14px rgba(0,0,0,.12);padding:14px 20px}
.date{display:inline-block;background:var(--red);color:#fff;font-size:10px;font-weight:600;padding:3px 8px}
.blog-box h4{margin-top:10px;font-size:18px;font-weight:600;color:var(--dark)}
.blog-box p{margin-top:8px;font-size:11px;line-height:1.6;color:var(--muted)}
.more{display:block;margin-top:8px;font-size:10px;font-weight:600;color:#555;letter-spacing:.5px}
.arrow{position:absolute;width:30px;height:30px;background:#555;color:#fff;font-size:14px;line-height:30px;text-align:center}
.post{position:absolute;left:667px;width:360px;height:152px}
.post .ph{position:absolute;left:0;top:0;width:165px;height:152px}
.post .body{position:absolute;left:175px;top:0;width:185px}
.post h4{margin-top:10px;font-size:16px;font-weight:600;color:var(--dark)}
.post p{margin-top:6px;font-size:11px;line-height:1.55;color:var(--muted)}

/* contact */
.contact{position:absolute;top:4064px;left:0;width:1200px;height:587px;background:radial-gradient(ellipse at 70% 20%,#5a0c10 0%,#2a0a0c 45%,#120707 100%)}
.contact .section-title{color:#fff;top:108px}
.contact-intro{position:absolute;left:330px;top:166px;width:540px;text-align:center;font-size:12px;line-height:1.7;color:#bbb}
.info{position:absolute;top:246px;display:flex;gap:12px;color:#ddd;font-size:12px;line-height:1.6}
.info svg{flex:none;margin-top:2px}
.field{position:absolute;border:1px solid #9a8a8a;color:#ddd;font-size:12px;padding:8px 12px}
.contact .btn{left:535px;top:500px;width:130px;height:36px;line-height:36px}

/* footer */
.site-footer{position:absolute;top:4651px;left:0;width:1200px;height:111px;background:#fff}
.site-footer .brand{top:38px}
.copy{position:absolute;right:175px;top:75px;font-size:11px;color:#444}
.social{position:absolute;right:175px;top:36px;display:flex;gap:6px}
.social span{width:26px;height:26px;border-radius:50%;background:var(--red)}
.social span:nth-child(n+2){background:#222}
</style>
</head>
<body>

<header class="site-header">
  <div class="brand"><span class="mark"></span>VAULTMERROW</div>
  <div class="call">
    <svg width="16" height="16" viewBox="0 0 24 24"><path fill="#e0101e" d="M6.6 10.8a15 15 0 006.6 6.6l2.2-2.2a1 1 0 011-.25 11.4 11.4 0 003.6.6 1 1 0 011 1V20a1 1 0 01-1 1A17 17 0 013 4a1 1 0 011-1h3.5a1 1 0 011 1c0 1.25.2 2.45.6 3.6a1 1 0 01-.25 1z"/></svg>
    Call Us:888 555 0142
  </div>
  <nav class="nav"><span>HOME</span><span>SERVICES</span><span>ABOUT</span><span>RESOURCES</span><span>BLOG</span><span>CONTACT US</span></nav>
</header>

<section class="hero">
  <div class="hero-photo" role="img" aria-label="Businessman in a suit holding a glowing security shield with a padlock"></div>
  <svg class="hero-shape" width="1200" height="605" viewBox="0 0 1200 605">
    <path fill="#e0101e" d="M0,470 C250,560 450,585 600,585 C780,585 980,540 1200,420 L1200,450 C980,570 780,605 600,605 C440,605 240,585 0,500Z"/>
    <path fill="#fff" d="M0,500 C240,585 440,605 600,605 L0,605Z"/>
    <path fill="#fff" d="M600,605 C780,605 980,570 1200,450 L1200,605Z"/>
  </svg>
  <h1>Vaultmerrow</h1>
  <p>Sed ut perspiciatis unde omnis iste natus error sit voluptatem accusantium doloremque laudantium totam rem.</p>
  <a class="btn">GET STARTED</a>
  <div class="dots"><span></span><span></span><span></span><span class="on"></span></div>
</section>

<!-- services -->
<div class="ghost" style="top:760px">SERVICES</div>
<h2 class="section-title" style="top:798px">SERVICES</h2>

<div class="rule-h" style="top:1125px"></div>
<div class="rule-h" style="top:1388px"></div>
<div class="rule-v" style="left:442px;top:880px;height:760px"></div>
<div class="rule-v" style="left:750px;top:880px;height:760px"></div>

<div class="service" style="left:175px;top:888px"><div class="icon" role="img" aria-label="Consultant icon"></div><h3><span>Neuorrou</span> Suaestulo</h3><p>Sed ut perspiciatis unde omnis iste natus error sit voluptatem accusantium doloremque laudantium totam rem aperiam eaque ipsa quae.</p></div>
<div class="service" style="left:476px;top:888px"><div class="icon" role="img" aria-label="Security badge icon"></div><h3><span>Neuorrou</span> Suaestulo</h3><p>Sed ut perspiciatis unde omnis iste natus error sit voluptatem accusantium doloremque laudantium totam rem aperiam eaque ipsa quae.</p></div>
<div class="service" style="left:784px;top:888px"><div class="icon" role="img" aria-label="Locked screen icon"></div><h3><span>Neuorrou</span> Suaestulo</h3><p>Sed ut perspiciatis unde omnis iste natus error sit voluptatem accusantium doloremque laudantium totam rem aperiam eaque ipsa quae.</p></div>

<div class="service" style="left:175px;top:1150px"><div class="icon" role="img" aria-label="Presenter icon"></div><h3><span>Neuorrou</span> Suaestulo</h3><p>Sed ut perspiciatis unde omnis iste natus error sit voluptatem accusantium doloremque laudantium totam rem aperiam eaque ipsa quae.</p></div>
<div class="service" style="left:476px;top:1150px"><div class="icon" role="img" aria-label="Shield with tick icon"></div><h3><span>Neuorrou</span> Suaestulo</h3><p>Sed ut perspiciatis unde omnis iste natus error sit voluptatem accusantium doloremque laudantium totam rem aperiam eaque ipsa quae.</p></div>
<div class="service" style="left:784px;top:1150px"><div class="icon" role="img" aria-label="Support agent icon"></div><h3><span>Neuorrou</span> Suaestulo</h3><p>Sed ut perspiciatis unde omnis iste natus error sit voluptatem accusantium doloremque laudantium totam rem aperiam eaque ipsa quae.</p></div>

<div class="service" style="left:175px;top:1413px"><div class="icon" role="img" aria-label="Verified person icon"></div><h3><span>Neuorrou</span> Suaestulo</h3><p>Sed ut perspiciatis unde omnis iste natus error sit voluptatem accusantium doloremque laudantium totam rem aperiam eaque ipsa quae.</p></div>
<div class="service" style="left:476px;top:1413px"><div class="icon" role="img" aria-label="Settings person icon"></div><h3><span>Neuorrou</span> Suaestulo</h3><p>Sed ut perspiciatis unde omnis iste natus error sit voluptatem accusantium doloremque laudantium totam rem aperiam eaque ipsa quae.</p></div>
<div class="service" style="left:784px;top:1413px"><div class="icon" role="img" aria-label="Folder icon"></div><h3><span>Neuorrou</span> Suaestulo</h3><p>Sed ut perspiciatis unde omnis iste natus error sit voluptatem accusantium doloremque laudantium totam rem aperiam eaque ipsa quae.</p></div>

<!-- about -->
<div class="ghost" style="top:1725px">ABOUT</div>
<h2 class="section-title" style="top:1763px">ABOUT</h2>
<div class="about-art" role="img" aria-label="Shield shaped collage of data security technology imagery"></div>
<p class="about-lead">Sed ut perspiciatis unde omnis iste natus ersit voluptatem accusantium doloremqueedtenspici atis unde omnis istoltatem accusantium</p>
<p class="about-copy" style="top:1972px">Sed ut perspiciatis unde omnis iste natus error sit voluptatem accusantium doloremque laudantium totam rem aperiam eaque ipsa quae ab illo inventore veritatis et quasi architecto beatae vitae dicta sunt explicabo. Nemo enim ipsam voluptatem quia voluptas sit aspernatur aut odit aut fugit sed quia consequuntur magni dolores eos qui ratione voluptatem sequi nesciunt neque porro quisquam est qui dolorem ipsum quia dolor sit amet.</p>
<p class="about-copy" style="top:2160px">Sed ut perspiciatis unde omnis iste natus error sit voluptatem accusantium doloremque laudantium totam rem aperiam eaque ipsa quae ab illo inventore veritatis et quasi architecto beatae vitae dicta sunt explicabo. Nemo enim ipsam voluptatem quia voluptas sit aspernatur aut odit aut fugit sed quia consequuntur magni dolores eos qui ratione voluptatem sequi nesciunt neque porro quisquam est qui dolorem ipsum quia dolor sit amet.</p>

<!-- resources -->
<div class="resources-bg"></div>
<div class="ghost" style="top:2528px;color:#e6e6e6">RESOURCES</div>
<h2 class="section-title" style="top:2566px">RESOURCES</h2>

<div class="res-card" style="left:175px;top:2661px"><div class="ph" role="img" aria-label="Colleagues working at a laptop" style="background:linear-gradient(160deg,#a9a39a,#4a4640 70%,#1f1d1b)"></div><h4>Sed ut perspiciatis unde iste natust volupm</h4></div>
<div class="res-card" style="left:460px;top:2661px"><div class="ph" role="img" aria-label="Two colleagues reviewing documents in an office" style="background:linear-gradient(160deg,#bfbfbf,#5d5b58 60%,#262422)"></div><h4>Sed ut perspiciatis unde iste natust volupm</h4></div>
<div class="res-card" style="left:752px;top:2661px"><div class="ph" role="img" aria-label="Hand touching a digital padlock interface" style="background:linear-gradient(160deg,#2a5fa0,#10305a 60%,#081a33)"></div><h4>Sed ut perspiciatis unde iste natust volupm</h4></div>
<div class="res-card" style="left:175px;top:2877px"><div class="ph" role="img" aria-label="Hand reaching toward a floating digital screen" style="background:linear-gradient(160deg,#d8d8d8,#6b6d70 60%,#2b2c2e)"></div><h4>Sed ut perspiciatis unde iste natust volupm</h4></div>
<div class="res-card" style="left:460px;top:2877px"><div class="ph" role="img" aria-label="Person working at a computer in a dim room" style="background:linear-gradient(160deg,#7a5a3c,#3a2a1c 60%,#150f0a)"></div><h4>Sed ut perspiciatis unde iste natust volupm</h4></div>
<div class="res-card" style="left:752px;top:2877px"><div class="ph" role="img" aria-label="Person using a laptop with security overlays" style="background:linear-gradient(160deg,#3e6fa8,#1a3558 60%,#0a1526)"></div><h4>Sed ut perspiciatis unde iste natust volupm</h4></div>

<!-- blog -->
<div class="ghost" style="top:3273px">LATEST BLOG</div>
<h2 class="section-title" style="top:3300px">LATEST BLOG</h2>
<p class="blog-intro">Sed ut perspiciatis unde omnis iste natus error sit voluptatem accusantium doloremque laudantu. Ac totam rem aperiedi ut perspiciatis unde omnis iste natus error sit voluptatem accusantiu.</p>

<div class="blog-hero">
  <div class="ph" role="img" aria-label="Hand touching glowing digital security icons"></div>
  <div class="blog-box">
    <span class="date">Feb 15 2019</span>
    <h4>Lorem ipsum dolormevol</h4>
    <p>Serror sit voluptatem accusantium doloremque laudantium, totam rem aperiam eaque ipsa quae ab illoquasi architec.</p>
    <span class="more">READ MORE</span>
  </div>
  <div class="arrow" style="left:432px;top:330px">&#8250;</div>
  <div class="arrow" style="left:432px;top:366px;background:#999">&#8249;</div>
</div>

<div class="post" style="top:3445px"><div class="ph" role="img" aria-label="Hand pointing at a digital security display" style="background:linear-gradient(160deg,#6d7580,#2c3036)"></div><div class="body"><span class="date">Feb 15 2019</span><h4>Lorem ipsum dolorme</h4><p>Serror sit voluptatem accusantium doloremque laudantiu sotu.</p><span class="more">READ MORE</span></div></div>
<div class="post" style="top:3613px"><div class="ph" role="img" aria-label="Businessman touching a virtual interface" style="background:linear-gradient(160deg,#9aa0a6,#4a4e53)"></div><div class="body"><span class="date">Feb 15 2019</span><h4>Lorem ipsum dolorme</h4><p>Serror sit voluptatem accusantium doloremque laudantiu sotu.</p><span class="more">READ MORE</span></div></div>
<div class="post" style="top:3778px"><div class="ph" role="img" aria-label="Glowing padlock on a blue circuit background" style="background:linear-gradient(160deg,#2b6cb0,#0c2748)"></div><div class="body"><span class="date">Feb 15 2019</span><h4>Lorem ipsum dolorme</h4><p>Serror sit voluptatem accusantium doloremque laudantiu sotu.</p><span class="more">READ MORE</span></div></div>

<!-- contact -->
<section class="contact">
  <h2 class="section-title">CONTACT US</h2>
  <p class="contact-intro">Sed ut perspiciatis unde omnis iste natus error sit voluptatem accusantium doloremque laudantu. Ac totam rem aperiedi ut perspiciatis unde omnis iste natus error sit voluptatem.</p>
  <div class="info" style="left:345px">
    <svg width="16" height="16" viewBox="0 0 24 24"><path fill="#e0101e" d="M12 2a7 7 0 00-7 7c0 5 7 13 7 13s7-8 7-13a7 7 0 00-7-7zm0 9.5A2.5 2.5 0 1112 6.5a2.5 2.5 0 010 5z"/></svg>
    <div>412 Harbour Lane,<br>Northgate, Qld</div>
  </div>
  <div class="info" style="left:545px">
    <svg width="16" height="16" viewBox="0 0 24 24"><path fill="#e0101e" d="M6.6 10.8a15 15 0 006.6 6.6l2.2-2.2a1 1 0 011-.25 11.4 11.4 0 003.6.6 1 1 0 011 1V20a1 1 0 01-1 1A17 17 0 013 4a1 1 0 011-1h3.5a1 1 0 011 1c0 1.25.2 2.45.6 3.6a1 1 0 01-.25 1z"/></svg>
    <div>Phone:<br>734 555 0190</div>
  </div>
  <div class="info" style="left:705px">
    <svg width="16" height="16" viewBox="0 0 24 24"><path fill="#e0101e" d="M3 5h18v14H3zm2 2v.5l7 4.5 7-4.5V7z"/></svg>
    <div>info@vaultmerrow.com.au<br>hello@vaultmerrow.com.au</div>
  </div>
  <div class="field" style="left:276px;top:317px;width:318px;height:34px">Name</div>
  <div class="field" style="left:276px;top:365px;width:318px;height:34px">Email</div>
  <div class="field" style="left:276px;top:413px;width:318px;height:34px">Phone</div>
  <div class="field" style="left:610px;top:317px;width:311px;height:130px">Message</div>
  <a class="btn">SUBMIT</a>
</section>

<footer class="site-footer">
  <div class="brand"><span class="mark"></span>VAULTMERROW</div>
  <div class="social"><span></span><span></span><span></span><span></span></div>
  <div class="copy">© 2019 All Rights Are Reserved. <b>Terms of Use</b> | <b>Privacy Policy</b></div>
</footer>

</body>
</html>
```